One of a kind service business!

We are the only ocean freight auditing company in the entire world that does what we do. We provide a innovative service in auditing our clients invoices for billing errors as it relates to the import and export of their products anywhere in the world. We'd like to retain the current logo - but we are open to any interesting concepts that can complete the card.

Target Market(s)

C-Level and Senior Financial executives

Industry/Entity Type

Auditing

Requirements
Must have

• ONE SIDED ONLY
Should not have
• no cartoonish images

```html
<!DOCTYPE html>
<html lang="en">
<head>
<meta charset="utf-8">
<title>Tidewell Audit – Business Card</title>
<link href="https://fonts.googleapis.com/css2?family=Quicksand:wght@400;500;700&display=swap" rel="stylesheet">
<style>
  :root {
    --backdrop: #e4e4e4;
    --card-dark: #0d0d0d;
    --card-dark-top: #232323;
    --card-light: #ffffff;
    --ink-light: #ffffff;
    --ink-muted: #a9a9a9;
    --brand-blue: #4fb3e6;
    --divider: #e8e8e8;
  }
  html, body {
    margin: 0;
    padding: 0;
    width: 1200px;
    height: 1027px;
    overflow: hidden;
    background: var(--backdrop);
    font-family: "Quicksand", sans-serif;
  }
  .canvas {
    position: relative;
    width: 1200px;
    height: 1027px;
  }
  .card {
    position: absolute;
    top: 375px;
    width: 552px;
    height: 349px;
    border-radius: 40px;
    overflow: hidden;
    box-shadow: 0 6px 14px rgba(0,0,0,0.25);
  }
  .card--front {
    left: 35px;
    background: linear-gradient(180deg, var(--card-dark-top) 0%, var(--card-dark) 40%, #050505 100%);
  }
  .card--front .sheen {
    position: absolute;
    left: 0;
    right: 0;
    top: 78px;
    height: 22px;
    background: linear-gradient(180deg, rgba(255,255,255,0) 0%, rgba(255,255,255,0.07) 50%, rgba(255,255,255,0) 100%);
  }
  .card--back {
    left: 618px;
    background: var(--card-light);
  }
  .brand {
    position: absolute;
    display: flex;
    align-items: center;
    gap: 7px;
    font-weight: 700;
    font-size: 27px;
    letter-spacing: 0.3px;
    color: var(--brand-blue);
    white-space: nowrap;
  }
  .brand__mark {
    width: 12px;
    height: 12px;
    background: var(--brand-blue);
  }
  .card--front .brand { left: 36px; top: 157px; }
  .card--back .brand { left: 50%; top: 157px; transform: translateX(-50%); }
  .divider {
    position: absolute;
    left: 258px;
    top: 57px;
    width: 2px;
    height: 221px;
    background: var(--divider);
  }
  .identity {
    position: absolute;
    left: 291px;
    top: 44px;
    width: 160px;
  }
  .identity__name {
    margin: 0;
    font-weight: 700;
    font-size: 19px;
    color: var(--ink-light);
    letter-spacing: 0.3px;
  }
  .identity__role {
    margin: 0;
    text-align: right;
    font-size: 12px;
    color: var(--ink-muted);
  }
  .contact {
    position: absolute;
    left: 285px;
    top: 176px;
    margin: 0;
    padding: 0;
    list-style: none;
    font-size: 12px;
    line-height: 15.6px;
    color: var(--ink-muted);
    letter-spacing: 0.3px;
  }
  .contact b {
    color: var(--ink-light);
    font-weight: 700;
    margin-right: 6px;
  }
</style>
</head>
<body>
  <main class="canvas">
    <section class="card card--front" aria-label="Card front">
      <div class="sheen"></div>
      <div class="brand"><span class="brand__mark"></span>Tidewell Audit</div>
      <div class="divider"></div>
      <div class="identity">
        <p class="identity__name">Daniel Marsh</p>
        <p class="identity__role">CEO</p>
      </div>
      <ul class="contact">
        <li>Harbor Point Center, Lindenweg 12</li>
        <li>Brno - Czech Republic 602 00</li>
        <li><b>p</b>+420 555 014 231</li>
        <li><b>m</b>+420 555 019 874</li>
        <li><b>USA</b>+1 555 201 4480</li>
        <li><b>f</b>+420 555 014 232</li>
        <li><b>e</b>daniel@tidewellaudit.net</li>
        <li><b>w</b>www.tidewellaudit.net</li>
      </ul>
    </section>
    <section class="card card--back" aria-label="Card back">
      <div class="brand"><span class="brand__mark"></span>Tidewell Audit</div>
    </section>
  </main>
</body>
</html>
```